Halverstone Minerals Web Design

Require a Web page design for an international mining and private investment company currently based in Dubai, UAE. I would like to view designs that incorporate our current corporate logo design aimed at communicating global business development/expansion across a diversity of commodities within the mining and investment sectors.

We are a global organisation with global experience and strategy with specific business development focus in Africa, Central and South America.

Target Market(s)

Mining industry, finance, fund raising, brokering, private equity and public stock exchanges.

Industry/Entity Type

Mining

Number of Pages Required

5+ page

Font styles to use
Sans Serif

Colors

Designer to choose colors to be used in the design.

Requirements
Must have
• Corporate logo, description of who we are, what we do, corporate mission, vision & strategy.
Nice to have
• Inclusion of images, photos, interactive maps/graphics and video.

```html
<!DOCTYPE html>
<html lang="en">
<head>
<meta charset="utf-8">
<title>Halverstone Minerals</title>
<link href="https://fonts.googleapis.com/css2?family=Barlow:wght@400;500;600&family=Poppins:wght@500;600;700&display=swap" rel="stylesheet">
<style>
:root{
  --ink:#161616;
  --dark:#1d1d1d;
  --dark-2:#242424;
  --gold:#d2a95a;
  --gold-light:#e8c988;
  --gold-deep:#b88a3c;
  --paper:#ececea;
  --white:#ffffff;
  --muted:#8a8a8a;
  --text:#3a3a3a;
}
*{box-sizing:border-box;margin:0;padding:0}
html,body{width:1200px;height:2927px;overflow:hidden}
body{font-family:"Barlow",Arial,sans-serif;background:var(--paper);color:var(--text);position:relative}
.wrap{position:absolute;left:234px;width:732px}
h1,h2,h3,.heading{font-family:"Poppins",Arial,sans-serif}

/* header */
.topbar{position:absolute;top:0;left:0;width:1200px;height:74px;background:var(--ink)}
.brand{position:absolute;left:234px;top:22px;display:flex;align-items:center;gap:10px}
.brand-mark{width:30px;height:30px;background:var(--gold)}
.brand-name{font-family:"Barlow",sans-serif;font-weight:600;font-size:18px;color:var(--gold);letter-spacing:.5px}
.contact-top{position:absolute;right:234px;top:20px;display:flex;gap:10px;align-items:center}
.circle-icon{width:32px;height:32px;border-radius:50%;background:var(--gold);display:flex;align-items:center;justify-content:center}
.contact-top p{font-size:11px;color:#ddd;line-height:16px}
.contact-top strong{color:var(--gold);font-weight:500;font-size:13px}
.mainnav{position:absolute;top:74px;left:0;width:1200px;height:32px;background:linear-gradient(180deg,var(--gold-light),var(--gold));display:flex;padding-left:234px;gap:28px;align-items:center}
.mainnav a{font-size:10.5px;text-transform:uppercase;color:#2a2113;text-decoration:none;font-weight:500;letter-spacing:.3px}

/* hero */
.hero{position:absolute;top:106px;left:0;width:1200px;height:480px;background:radial-gradient(ellipse at 65% 45%,#7a5a3a 0%,#4a3322 45%,#251a12 100%)}
.hero h1{position:absolute;left:234px;top:152px;width:370px;color:var(--white);font-size:23px;line-height:31px;font-weight:600}
.btn{display:inline-block;background:linear-gradient(180deg,var(--gold-light),var(--gold-deep));color:#2a2113;font-size:10px;text-transform:uppercase;font-weight:600;padding:9px 16px;letter-spacing:.3px}
.hero .btn{position:absolute;left:234px;top:300px}
.hero-curve{position:absolute;top:540px;left:0}
.slider-dots{position:absolute;top:588px;left:572px;display:flex;gap:6px}
.slider-dots span{width:24px;height:24px;border-radius:50%;display:flex;align-items:center;justify-content:center}
.dot-dark{background:#222}.dot-gold{background:var(--gold)}

/* feature tiles */
.tiles{top:663px;display:flex;gap:18px}
.tile{width:232px;text-align:center}
.tile .photo{height:160px}
.tile p{margin-top:20px;font-size:15px;color:#2a2a2a}

/* who we are */
.who{position:absolute;top:903px;left:0;width:1200px;height:488px;background:var(--dark)}
.who-photo{position:absolute;left:226px;top:57px;width:367px;height:230px;border:3px solid var(--gold-deep);background:radial-gradient(ellipse at 50% 40%,#6a5238,#2a2018)}
.who-text{position:absolute;left:628px;top:55px;width:340px}
.who-text h2{color:var(--white);font-size:22px;font-weight:600}
.who-text .lead{color:var(--white);font-size:12px;line-height:18px;margin-top:10px;font-weight:500}
.who-text .body{color:#a0a0a0;font-size:11px;line-height:18px;margin-top:14px}
.more{display:inline-block;margin-top:18px;color:var(--gold);font-size:11px;border-bottom:1px solid var(--gold);padding-bottom:3px}
.pillars{position:absolute;left:234px;top:340px;display:flex;gap:40px}
.pillar{width:220px;display:flex;gap:14px}
.pillar h3{color:var(--white);font-size:14px;font-weight:500;font-family:"Barlow",sans-serif}
.pillar p{color:#8a8a8a;font-size:10.5px;line-height:17px;margin-top:8px}

/* projects */
.projects{position:absolute;top:1391px;left:0;width:1200px;height:406px;background:var(--paper)}
.projects-photo{position:absolute;left:0;top:0;width:599px;height:406px;background:linear-gradient(160deg,#d6a25a 0%,#a66f38 40%,#5a3b22 100%)}
.projects-title{position:absolute;left:300px;top:135px;text-align:center;width:230px}
.projects-title h2{color:var(--white);font-size:34px;line-height:38px;font-weight:700}
.projects-title .btn{margin-top:14px;background:#4a3626;color:#e8d9c0}
.project-list{position:absolute;left:634px;top:62px;width:330px}
.project-list li{list-style:none;display:flex;gap:14px;margin-bottom:26px;font-size:11px;line-height:18px;color:#555}
.project-list b{color:#222}

/* team */
.team{position:absolute;top:1797px;left:0;width:1200px;height:384px;background:var(--dark-2)}
.team h2{position:absolute;top:45px;width:100%;text-align:center;color:var(--white);font-size:22px;font-weight:600}
.team-row{position:absolute;left:234px;top:92px;display:flex;gap:5px}
.member{width:180px;height:248px;text-align:center}
.member .photo{height:180px}
.member h3{font-family:"Barlow",sans-serif;color:var(--white);font-size:15px;font-weight:500;margin-top:12px}
.member p{color:#999;font-size:10px;line-height:13px;margin-top:3px}
.member.active{background:var(--gold)}
.member.active p{color:#4a3a1e}

/* blog + testimonials */
.lower{top:2230px}
.lower h2{font-size:22px;color:#1f1f1f;font-weight:600}
.blog{position:absolute;left:0;top:0;width:370px}
.post{display:flex;gap:18px;margin-top:18px}
.post .photo{width:136px;height:86px;flex:none}
.post h4{font-size:13px;color:#222;font-weight:500}
.post .meta{font-size:9.5px;color:#777;margin-top:4px}
.post .meta span{color:var(--gold-deep)}
.post p{font-size:10px;color:#777;line-height:16px;margin-top:8px}
.testimonials{position:absolute;left:394px;top:0;width:338px}
.quote-card{background:var(--white);margin-top:14px;padding:20px 20px 20px 42px;position:relative;height:198px}
.quote-card .mark{position:absolute;left:18px;top:16px;color:#aaa;font-size:22px;font-family:"Poppins",sans-serif}
.quote-card p{font-size:10.5px;line-height:17px;color:#666}
.quote-card .who-said{margin-top:10px;color:#222;font-size:13px}
.quote-card .role{font-size:10px;color:#888}

/* footer */
.footer{position:absolute;top:2544px;left:0;width:1200px;height:383px;background:#1b1b1b}
.footer-scene{position:absolute;left:0;top:0;width:1200px;height:120px;background:linear-gradient(180deg,#3a3a3a 0%,#262626 100%)}
.footer-nav{position:absolute;top:140px;left:0;width:1200px;display:flex;justify-content:center;gap:24px}
.footer-nav a{font-size:10.5px;color:#bbb;text-decoration:none}
.footer-cols{position:absolute;left:234px;top:195px;display:flex;gap:0}
.fcol{width:150px}
.fcol h4{color:var(--white);font-size:13px;font-weight:500}
.fcol p{color:#999;font-size:10px;line-height:15px;margin-top:6px}
.fcontact{width:250px;padding-left:14px}
.fitem{display:flex;gap:12px;align-items:center;margin-bottom:18px}
.fitem p{font-size:10px;color:#999;line-height:14px}
.fitem strong{color:var(--white);font-weight:500;font-size:11px}
.newsletter h4{color:var(--white);font-size:13px;font-weight:500}
.newsletter .field{width:170px;height:30px;background:var(--white);margin-top:10px;font-size:10px;color:#aaa;padding:9px 10px}
.newsletter .btn{margin-top:12px;padding:7px 14px}
.footer-bottom{position:absolute;top:340px;left:234px;width:732px;border-top:1px solid #333;padding-top:10px;display:flex;justify-content:space-between;align-items:center}
.footer-bottom p{font-size:10px;color:#888}
.socials{display:flex;gap:6px}
.socials span{width:22px;height:22px;background:#cfcfcf}
</style>
</head>
<body>

<header class="topbar">
  <div class="brand"><span class="brand-mark"></span><span class="brand-name">Halverstone Minerals</span></div>
  <div class="contact-top">
    <span class="circle-icon"><svg width="14" height="14" viewBox="0 0 24 24"><path fill="#1b1b1b" d="M6.6 10.8a15 15 0 0 0 6.6 6.6l2.2-2.2c.3-.3.7-.4 1-.2 1.1.4 2.3.6 3.6.6.6 0 1 .4 1 1V20c0 .6-.4 1-1 1A17 17 0 0 1 3 4c0-.6.4-1 1-1h3.5c.6 0 1 .4 1 1 0 1.3.2 2.5.6 3.6.1.3 0 .7-.2 1z"/></svg></span>
    <p>Have a question? call us today<br><strong>+224 600 118 274 | +61 400 372 906</strong></p>
  </div>
</header>
<nav class="mainnav">
  <a>Executive Summary</a><a>Team &amp; Experience</a><a>Commercial</a><a>Business Model</a><a>Strategy</a><a>Contact</a>
</nav>

<section class="hero" role="img" aria-label="Miners in hard hats drilling a rock face underground">
  <h1>A platform for execution of global mining projects with an initial focus on South America, Central America &amp; Africa.</h1>
  <a class="btn">Get Started</a>
</section>
<svg class="hero-curve" width="1200" height="60" viewBox="0 0 1200 60">
  <path d="M0 44 Q600 -20 1200 44 L1200 60 L0 60Z" fill="#ececea"/>
  <path d="M0 44 Q600 -20 1200 44" fill="none" stroke="#d2a95a" stroke-width="6"/>
</svg>
<div class="slider-dots">
  <span class="dot-dark"><svg width="8" height="8" viewBox="0 0 8 8"><path d="M5.5 1 2.5 4l3 3" stroke="#fff" stroke-width="1.5" fill="none"/></svg></span>
  <span class="dot-gold"><svg width="8" height="8" viewBox="0 0 8 8"><path d="M2.5 1l3 3-3 3" stroke="#222" stroke-width="1.5" fill="none"/></svg></span>
</div>

<section class="wrap tiles">
  <div class="tile"><div class="photo" role="img" aria-label="Hands together holding a young plant" style="background:linear-gradient(135deg,#2a3a40,#8a7a6a)"></div><p>Social Responsibility</p></div>
  <div class="tile"><div class="photo" role="img" aria-label="Smiling business team around a meeting table" style="background:linear-gradient(135deg,#c9b59a,#e8e2d8)"></div><p>Investors</p></div>
  <div class="tile"><div class="photo" role="img" aria-label="Hand touching a glowing world network map" style="background:linear-gradient(135deg,#1a2f5a,#4a78b8)"></div><p>Contact Us</p></div>
</section>

<section class="who">
  <div class="who-photo" role="img" aria-label="Mining engineers in hard hats inside a tunnel"></div>
  <div class="who-text">
    <h2>Who We Are</h2>
    <p class="lead">Strong industry connections &amp; networks in Africa, South America &amp; Australia.</p>
    <p class="body">Newly formed company to create a platform for execution of global mining projects with an initial focus on South America, Central America &amp; Africa. Strong executive &amp; management team with A to Z in all facets of mining, finance &amp; operations. Properly capitalized to execute its mandate.</p>
    <a class="more">Learn More About Us &nbsp;+</a>
  </div>
  <div class="pillars">
    <div class="pillar">
      <svg width="36" height="36" viewBox="0 0 36 36" fill="none" stroke="#d2a95a" stroke-width="2"><circle cx="16" cy="20" r="13"/><circle cx="16" cy="20" r="7"/><circle cx="16" cy="20" r="2" fill="#d2a95a"/><path d="M16 20 32 4M26 4h6v6"/></svg>
      <div><h3>Our Mission</h3><p>Class aptent taciti sociosqu ad litora torquent per conubia nostra per inceptos aeos mauris ut aliquam massa nisl quis neques suspendisse in orci enim.</p></div>
    </div>
    <div class="pillar">
      <svg width="36" height="36" viewBox="0 0 36 36" fill="none" stroke="#d2a95a" stroke-width="2"><path d="M3 18s6-10 15-10 15 10 15 10-6 10-15 10S3 18 3 18z"/><circle cx="18" cy="18" r="5"/><path d="M18 2v3M8 5l2 3M28 5l-2 3"/></svg>
      <div><h3>Our Vision</h3><p>Class aptent taciti sociosqu ad litora torquent per conubia nostra per inceptos aeos mauris ut aliquam massa nisl quis neques suspendisse in orci enim.</p></div>
    </div>
    <div class="pillar">
      <svg width="36" height="36" viewBox="0 0 36 36" fill="none" stroke="#d2a95a" stroke-width="2"><path d="M8 32h20M10 28h16M12 28l2-12h8l2 12M14 16l-3-6 7-6 7 6-3 6"/></svg>
      <div><h3>Our Strategy</h3><p>Class aptent taciti sociosqu ad litora torquent per conubia nostra per inceptos aeos mauris ut aliquam massa nisl quis neques suspendisse in orci enim.</p></div>
    </div>
  </div>
</section>

<section class="projects">
  <div class="projects-photo" role="img" aria-label="Engineer overlooking an open-pit mine at sunset"></div>
  <div class="projects-title">
    <h2>PROJECT<br>EXPERIENCE</h2>
    <a class="btn">View All Project</a>
  </div>
  <ul class="project-list">
    <li><svg width="18" height="18" viewBox="0 0 18 18" fill="none" stroke="#d2a95a" stroke-width="1.6"><path d="M2 5q7-5 14 0M9 2l-4 14"/></svg><span>Exploration experts in <b>Brazil, Burkina Faso, Cote d'Ivoire, Colombia, Chile, Ghana, Guinea, Gabon, Togo, Mali, Niger, Nigeria, Peru, Saudi Arabia</b> &amp; more recently the copper belt in <b>Zambia.</b></span></li>
    <li><svg width="18" height="18" viewBox="0 0 18 18" fill="none" stroke="#d2a95a" stroke-width="1.6"><path d="M2 5q7-5 14 0M9 2l-4 14"/></svg><span><b>Kestrel Ridge Mine</b> - an underground polymetallic (Zinc, lead, gold &amp; copper) mine located in the west of Tasmania's west coast, Australia. 2017 production target: over 65,000 tonnes of zinc in zinc concentrate over 18,000 tonnes of lead.</span></li>
    <li><svg width="18" height="18" viewBox="0 0 18 18" fill="none" stroke="#d2a95a" stroke-width="1.6"><path d="M2 5q7-5 14 0M9 2l-4 14"/></svg><span>The <b>Vale Dourado</b> facility in South East Brazil with an installed capacity to produce approximately 6 million tons of iron ore annually from the Pedra Alta &amp; Cedro mines &amp; Boa Vista Mines belonging to Ferrocorp Brazil.</span></li>
  </ul>
</section>

<section class="team">
  <h2>Executive Team</h2>
  <div class="team-row">
    <div class="member"><div class="photo" role="img" aria-label="Portrait of the chairman" style="background:linear-gradient(180deg,#c8ccd2,#5a6270)"></div><h3>Graham Whitcombe</h3><p>Chairman</p></div>
    <div class="member"><div class="photo" role="img" aria-label="Portrait of the CEO" style="background:linear-gradient(180deg,#d8dce0,#4a5260)"></div><h3>Daniel Okafor</h3><p>CEO</p></div>
    <div class="member active"><div class="photo" role="img" aria-label="Portrait of the CFO" style="background:linear-gradient(180deg,#b8c4d0,#4a5a70)"></div><h3>Peter Marlowe</h3><p>CFO</p></div>
    <div class="member"><div class="photo" role="img" aria-label="Portrait of the technical director" style="background:linear-gradient(180deg,#c0c8d0,#3a4250)"></div><h3>Rafael Duarte Lins</h3><p>Technical Director and<br>Country Manager (Brazil)</p></div>
  </div>
</section>

<section class="wrap lower">
  <div class="blog">
    <h2>From the Blog</h2>
    <div class="post"><div class="photo" role="img" aria-label="Mining crew in a tunnel" style="background:linear-gradient(135deg,#2a3040,#6a5a48)"></div><div><h4>Lorem Ipsum charsets layouts</h4><p class="meta">By <span>Evan Hollis</span> | 03 May 2018</p><p>Class aptent taciti sociosqu ad litora torquent per conubia himenaeos. Mauris in erat justo.</p></div></div>
    <div class="post"><div class="photo" role="img" aria-label="Haul trucks at a quarry" style="background:linear-gradient(135deg,#8a9aa8,#c9a24a)"></div><div><h4>Lorem Ipsum charsets layouts</h4><p class="meta">By <span>Evan Hollis</span> | 03 May 2018</p><p>Class aptent taciti sociosqu ad litora torquent per conubia himenaeos. Mauris in erat justo.</p></div></div>
  </div>
  <div class="testimonials">
    <h2>Testimonials</h2>
    <div class="quote-card">
      <span class="mark">&ldquo;</span>
      <p>Class aptent taciti sociosqu ad litora torquent per conubia nostra, per inceptos himenaeos. Mauris in condimentum sit amet a augue. Sed non neque elit. Sed ut imperdiet nisi. Proin condimentum fermentum nunc. Etiam pharetra, erat sed fermentum feugiat, velit mauris egestas quam, ut aliquam massa nisl quis neque. Suspendisse in orci enim.</p>
      <p class="who-said">- Mark Fenwick</p>
      <p class="role">Lorem Ipsum dolor</p>
    </div>
  </div>
</section>

<footer class="footer">
  <div class="footer-scene" role="img" aria-label="Silhouettes of mining machinery and workers"></div>
  <nav class="footer-nav"><a>Executive Summary</a><a>Team &amp; Experience</a><a>Commercial</a><a>Business Model</a><a>Strategy</a><a>Contact</a></nav>
  <div class="footer-cols">
    <div class="fcol"><h4>Dubai, UAE</h4><p>Suite 212, Tower 3,<br>Marina Court,<br>Harbour Walk,<br>Creekside Quarter,<br>Dubai, UAE.</p></div>
    <div class="fcol"><h4>Guinea, West Africa</h4><p>Ratoma - Rue des<br>Palmiers,<br>Immeuble 17,<br>BP: 2290</p></div>
    <div class="fcontact">
      <div class="fitem"><span class="circle-icon"><svg width="14" height="14" viewBox="0 0 24 24"><path fill="#1b1b1b" d="M6.6 10.8a15 15 0 0 0 6.6 6.6l2.2-2.2c.3-.3.7-.4 1-.2 1.1.4 2.3.6 3.6.6.6 0 1 .4 1 1V20c0 .6-.4 1-1 1A17 17 0 0 1 3 4c0-.6.4-1 1-1h3.5c.6 0 1 .4 1 1 0 1.3.2 2.5.6 3.6.1.3 0 .7-.2 1z"/></svg></span><p>Call Us :<br><strong>+224 600 118 274<br>+61 400 372 906</strong></p></div>
      <div class="fitem"><span class="circle-icon"><svg width="14" height="14" viewBox="0 0 24 24" fill="none" stroke="#1b1b1b" stroke-width="2.2"><rect x="3" y="5" width="18" height="14"/><path d="M3 6l9 7 9-7"/></svg></span><p>Email Us :<br><strong>info@halverstoneminerals.com</strong></p></div>
    </div>
    <div class="newsletter"><h4>Subscribe Newsletter</h4><div class="field">Email Address</div><a class="btn">Subscribe</a></div>
  </div>
  <div class="footer-bottom">
    <p>© 2018 Halverstone Minerals. All Rights Reserved</p>
    <div class="socials"><span></span><span></span><span></span></div>
  </div>
</footer>

</body>
</html>
```